Business Card for a New Zealand IT Startup

I need a business card for VELTA Holdings. We are a young startup based in New Zealand working in internet marketing and web development. The design should have some element connected to New Zealand, such as wave, koru or silver fern, just don't use a kiwi bird.

```html
<!DOCTYPE html>
<html lang="en">
<head>
<meta charset="utf-8">
<title>VELTA Holdings – Business Card</title>
<link rel="stylesheet" href="https://fonts.googleapis.com/css2?family=Jost:wght@400;500;600&display=swap">
<style>
  :root {
    --brand-blue: #0a6ebd;
    --brand-orange: #f05a22;
    --wave-pale: #e2edf8;
    --wave-soft: #cfe1f3;
    --card-white: #ffffff;
    --text-grey: #4a4f55;
    --backdrop: #e9ebee;
  }
  * { box-sizing: border-box; margin: 0; padding: 0; }
  html, body {
    width: 1200px; height: 1040px; overflow: hidden;
    background: var(--backdrop);
    font-family: "Jost", sans-serif;
  }
  .canvas { position: relative; width: 1200px; height: 1040px; }
  .card {
    position: absolute; left: 180px;
    width: 840px; height: 480px;
    background: var(--card-white);
    border-radius: 24px; overflow: hidden;
    box-shadow: 0 4px 14px rgba(0,0,0,0.12);
  }
  .card--front { top: 27px; }
  .card--back { top: 533px; }
  .card__art { position: absolute; inset: 0; }

  .holder { position: absolute; left: 40px; bottom: 58px; color: var(--card-white); }
  .holder__name { font-size: 32px; font-weight: 400; letter-spacing: 1px; line-height: 1.1; }
  .holder__title { font-size: 18px; font-weight: 400; letter-spacing: 0.5px; margin-top: 2px; }

  .brand { position: absolute; display: flex; align-items: center; gap: 12px; }
  .brand__dot { width: 16px; height: 16px; border-radius: 50%; background: var(--brand-orange); }
  .brand__name { color: var(--brand-blue); font-weight: 600; font-size: 46px; letter-spacing: 1px; white-space: nowrap; line-height: 1; }
  .card--front .brand { left: 345px; top: 308px; }

  .contact { position: absolute; left: 560px; top: 62px; width: 250px; color: var(--text-grey); }
  .contact__address { font-size: 16px; line-height: 1.35; padding-bottom: 14px; }
  .contact__rule { height: 1px; background: var(--brand-blue); margin-bottom: 14px; }
  .contact__list { list-style: none; }
  .contact__item { display: flex; align-items: center; gap: 10px; font-size: 16px; line-height: 1.6; }
  .contact__icon { width: 15px; height: 15px; flex: none; }

  .card--back .brand { left: 50%; top: 150px; transform: translateX(-50%); }
  .back-web {
    position: absolute; left: 0; right: 0; top: 222px; text-align: center;
    color: var(--text-grey); font-size: 18px; letter-spacing: 3px;
  }
</style>
</head>
<body>
<main class="canvas">

  <section class="card card--front" aria-label="Business card front">
    <svg class="card__art" viewBox="0 0 840 480" width="840" height="480" aria-hidden="true">
      <path class="wave wave--back" d="M290 440 C390 400 470 470 570 430 S740 400 840 425 V480 H290 Z" fill="var(--wave-pale)"/>
      <path class="wave wave--line" d="M300 462 C400 425 480 490 580 452 S750 425 840 448" fill="none" stroke="var(--wave-soft)" stroke-width="4"/>
      <path class="band band--blue" d="M0 0 H400 C290 120 252 300 272 480 H0 Z" fill="var(--brand-blue)"/>
      <path class="band band--orange" d="M415 0 C305 120 267 300 288 480" fill="none" stroke="var(--brand-orange)" stroke-width="12"/>
    </svg>

    <div class="holder">
      <p class="holder__name">ARIA TANE</p>
      <p class="holder__title">CEO/FOUNDER</p>
    </div>

    <div class="brand">
      <span class="brand__name">VELTA Holdings</span>
      <span class="brand__dot"></span>
    </div>

    <div class="contact">
      <p class="contact__address">214 Harbour View Road<br>Wellington, New Zealand 6011</p>
      <div class="contact__rule"></div>
      <ul class="contact__list">
        <li class="contact__item">
          <svg class="contact__icon" viewBox="0 0 16 16" aria-hidden="true"><path d="M3 1 L6 1 L7 5 L5 6.5 C6 9 7 10 9.5 11 L11 9 L15 10 L15 13 C15 14 14 15 13 15 C6 15 1 10 1 3 C1 2 2 1 3 1 Z" fill="var(--brand-blue)"/></svg>
          <span>021 458 3307</span>
        </li>
        <li class="contact__item">
          <svg class="contact__icon" viewBox="0 0 16 16" aria-hidden="true"><rect x="4" y="1" width="8" height="14" rx="1.5" fill="none" stroke="var(--brand-blue)" stroke-width="1.6"/><circle cx="8" cy="12.5" r="0.9" fill="var(--brand-blue)"/></svg>
          <span>027 691 4820</span>
        </li>
        <li class="contact__item">
          <svg class="contact__icon" viewBox="0 0 16 16" aria-hidden="true"><rect x="1" y="6" width="14" height="8" rx="1" fill="var(--brand-blue)"/><rect x="4" y="2" width="8" height="5" fill="none" stroke="var(--brand-blue)" stroke-width="1.4"/></svg>
          <span>04 385 7162</span>
        </li>
        <li class="contact__item">
          <svg class="contact__icon" viewBox="0 0 16 16" aria-hidden="true"><rect x="1" y="3" width="14" height="10" rx="1" fill="var(--brand-blue)"/><path d="M1.5 3.5 L8 9 L14.5 3.5" fill="none" stroke="#fff" stroke-width="1.3"/></svg>
          <span>aria@veltaholdings.com</span>
        </li>
        <li class="contact__item">
          <svg class="contact__icon" viewBox="0 0 16 16" aria-hidden="true"><circle cx="8" cy="8" r="7" fill="var(--brand-blue)"/><path d="M1 8 H15 M8 1 C5 4 5 12 8 15 M8 1 C11 4 11 12 8 15" fill="none" stroke="#fff" stroke-width="1"/></svg>
          <span>www.veltaholdings.com</span>
        </li>
      </ul>
    </div>
  </section>

  <section class="card card--back" aria-label="Business card back">
    <svg class="card__art" viewBox="0 0 840 480" width="840" height="480" aria-hidden="true">
      <path class="wave wave--back" d="M0 360 C140 310 260 400 420 350 S700 310 840 345 V480 H0 Z" fill="var(--wave-pale)"/>
      <path class="wave wave--line" d="M0 400 C150 355 270 440 430 392 S710 355 840 388" fill="none" stroke="var(--wave-soft)" stroke-width="5"/>
      <path class="wave wave--line" d="M0 440 C150 400 280 475 440 432 S720 400 840 428" fill="none" stroke="var(--wave-soft)" stroke-width="4"/>
    </svg>
    <div class="brand">
      <span class="brand__name">VELTA Holdings</span>
      <span class="brand__dot"></span>
    </div>
    <p class="back-web">www.veltaholdings.com</p>
  </section>

</main>
</body>
</html>
```